Professional looking Roller Blind Discount Card that portrays quality at a value for money price!

We need a double sided business card designed as a discount card. Size 90mm wide x 55mm high.We would like it to look professional and portray quality at a value for money price point.I have uploaded a word document with a basic layout with the information we want included on each side of the card. Please put your own thought into the layout.

Contact Information for Business Card

As per word document attached.

```html
<!DOCTYPE html>
<html lang="en">
<head>
<meta charset="utf-8">
<title>Roller Blinds Discount Card</title>
<link href="https://fonts.googleapis.com/css2?family=Poppins:wght@400;500;600;700&family=Oswald:wght@700&family=Great+Vibes&display=swap" rel="stylesheet">
<style>
  :root {
    --brand-blue: #29abe2;
    --deep-blue: #1b7fd4;
    --light-blue: #5cc8f5;
    --ink: #4a4a4a;
    --paper: #ffffff;
    --backdrop: #a3a3a3;
  }
  * { margin: 0; padding: 0; box-sizing: border-box; }
  html, body { width: 1133px; height: 1200px; overflow: hidden; }
  body {
    background: var(--backdrop);
    font-family: "Poppins", sans-serif;
    position: relative;
  }
  .card {
    position: absolute;
    left: 116px;
    width: 900px;
    height: 515px;
    background: var(--paper);
    overflow: hidden;
  }
  .card--front { top: 50px; }
  .card--back { top: 635px; }

  /* Front */
  .offer-band {
    height: 141px;
    background: var(--brand-blue);
    display: flex;
    align-items: center;
    justify-content: center;
    gap: 6px;
  }
  .offer-title {
    color: var(--paper);
    font-weight: 700;
    font-size: 112px;
    line-height: 1;
    letter-spacing: 1px;
    padding-top: 8px;
  }
  .offer-rule { width: 108px; height: 20px; }
  .product-lines {
    text-align: center;
    color: var(--ink);
    font-size: 41px;
    line-height: 42px;
    margin-top: 18px;
  }
  .badges {
    display: flex;
    justify-content: center;
    gap: 46px;
    margin-top: 14px;
  }
  .badge { position: relative; width: 176px; height: 176px; }
  .badge svg { position: absolute; inset: 0; }
  .badge-text {
    position: absolute;
    inset: 0;
    display: flex;
    align-items: center;
    justify-content: center;
    text-align: center;
    color: var(--paper);
    font-family: "Oswald", sans-serif;
    font-weight: 700;
    font-size: 23px;
    line-height: 27px;
    text-shadow: 0 1px 2px rgba(0,0,0,.35);
  }
  .call-line {
    text-align: center;
    color: var(--ink);
    font-size: 40px;
    margin-top: 8px;
    line-height: 1.2;
  }
  .call-line .phone { color: var(--brand-blue); font-weight: 600; }

  /* Back */
  .title-band {
    height: 168px;
    background: var(--brand-blue);
    color: var(--paper);
    padding-left: 32px;
  }
  .title-main {
    font-weight: 700;
    font-size: 114px;
    line-height: 0.92;
    padding-top: 14px;
    letter-spacing: -1px;
  }
  .title-sub {
    font-weight: 500;
    font-size: 53px;
    line-height: 1;
    margin-top: -2px;
  }
  .window-photo {
    position: absolute;
    left: 36px;
    top: 185px;
    width: 559px;
    height: 237px;
    background: linear-gradient(90deg, #6e5a4f 0 18%, #5f7d4a 18% 60%, #7f9a6a 60% 88%, #a09080 88%);
  }
  .call-bar {
    position: absolute;
    left: 36px;
    top: 422px;
    width: 559px;
    height: 66px;
    background: var(--brand-blue);
    color: var(--paper);
    font-size: 41px;
    line-height: 66px;
    text-align: center;
  }
  .call-bar .phone { font-weight: 600; }
  .fabric-bubble {
    position: absolute;
    left: 628px;
    top: 195px;
    width: 230px;
    height: 160px;
  }
  .fabric-text {
    position: absolute;
    left: 644px;
    top: 222px;
    width: 198px;
    text-align: center;
    color: var(--paper);
    font-family: "Great Vibes", cursive;
    font-size: 28px;
    line-height: 32px;
    white-space: nowrap;
  }
  .company-name {
    position: absolute;
    left: 615px;
    top: 440px;
    width: 270px;
    text-align: center;
    color: var(--brand-blue);
    font-weight: 500;
    font-size: 28px;
    line-height: 1;
  }
</style>
</head>
<body>
  <section class="card card--front">
    <header class="offer-band">
      <svg class="offer-rule" viewBox="0 0 108 20"><rect y="3" width="108" height="2.5" fill="#fff"/><rect y="9" width="108" height="2.5" fill="#fff"/><rect y="15" width="108" height="2.5" fill="#fff"/></svg>
      <h1 class="offer-title">25% OFF</h1>
      <svg class="offer-rule" viewBox="0 0 108 20"><rect y="3" width="108" height="2.5" fill="#fff"/><rect y="9" width="108" height="2.5" fill="#fff"/><rect y="15" width="108" height="2.5" fill="#fff"/></svg>
    </header>
    <p class="product-lines">Quality Custom Made Roller Blinds<br>Blockout - screen - LightFiltering</p>
    <svg width="0" height="0" style="position:absolute">
      <defs>
        <linearGradient id="seal-fill" x1="0" y1="0" x2="0" y2="1">
          <stop offset="0" stop-color="#5cc8f5"/>
          <stop offset="1" stop-color="#1b7fd4"/>
        </linearGradient>
        <g id="seal">
          <circle cx="88" cy="88" r="81" fill="none" stroke="#29abe2" stroke-width="10" stroke-dasharray="3.2 3.2"/>
          <circle cx="88" cy="88" r="79" fill="#29abe2"/>
          <circle cx="88" cy="88" r="74" fill="#fff"/>
          <circle cx="88" cy="88" r="69" fill="url(#seal-fill)"/>
        </g>
      </defs>
    </svg>
    <div class="badges">
      <div class="badge"><svg viewBox="0 0 176 176"><use href="#seal"/></svg><div class="badge-text">FREE<br>in Home<br>Measure &amp;<br>Quote</div></div>
      <div class="badge"><svg viewBox="0 0 176 176"><use href="#seal"/></svg><div class="badge-text">Best Price<br>Guarantee</div></div>
      <div class="badge"><svg viewBox="0 0 176 176"><use href="#seal"/></svg><div class="badge-text">Family<br>Owned &amp;<br>Operated</div></div>
    </div>
    <p class="call-line">CALL <span class="phone">0400 123 456</span> TODAY!</p>
  </section>

  <section class="card card--back">
    <header class="title-band">
      <h2 class="title-main">ROLLER BLINDS</h2>
      <p class="title-sub">FREE in Home Meacure &amp; Quote</p>
    </header>
    <div class="window-photo" role="img" aria-label="Photo of a kitchen window looking out onto a green garden"></div>
    <p class="call-bar">CALL <span class="phone">0400 123 456</span> TODAY!</p>
    <svg class="fabric-bubble" viewBox="0 0 230 160">
      <defs>
        <linearGradient id="bubble-fill" x1="0" y1="0" x2="1" y2="1">
          <stop offset="0" stop-color="#6fd0f7"/>
          <stop offset="1" stop-color="#1b7fd4"/>
        </linearGradient>
      </defs>
      <path d="M115 8 C175 8 222 32 222 70 C222 108 175 132 115 132 C95 132 78 130 62 125 L40 152 L44 118 C20 107 8 90 8 70 C8 32 55 8 115 8 Z" fill="url(#bubble-fill)"/>
    </svg>
    <p class="fabric-text">Huge Selection<br>of Fabrics</p>
    <p class="company-name">B&amp;K INTERIORS</p>
  </section>
</body>
</html>
```